Bright Pelvicare Business Card

Need a business card for a surgical practice called Bright Pelvicare. We have recently selected a logo (attached). The business card will need to have two formats:
1) One with the logo/physician name/ contact info on the front and location information on the back.
2) One in "appointment reminder card" style with the logo/ contact info/ date/ time on the front and the location information on the back.

The front side should include the following information:
- Logo
- Rohan K. Desai, MD FACOG
- phone: 469-555-0182
- fax: 1-469-555-0317
- email: admin@brightpelvi.com
- website: www.brightpelvicare.com

The back side should have the office locations listed:
4518 Kestrel Ave, Plano, TX 75198
3920 Bramwell Rd, Plano, TX 75147
2245 Silverpine Ln, Irving, TX 75163
815 W Garnet Ave S310, Dallas, TX 75284
3614 Lantern Blvd, Grand Prairie, TX 75179
7405 Amberly Crest Dr, San Antonio, TX 78391
5812 Tolliver Rd, Pasadena, TX 77639

Target Market(s)

1. Other physicians who might refer patients
2. Female patients

Industry/Entity Type

Business

Font styles to use
Other font styles liked:
• Tahoma for lettering

Requirements
Must have
• As per the instructions
Should not have
• No other images needed -- please try to keep font consistent with logo design. Can use Tahoma as the font for lettering.

```html
<!DOCTYPE html>
<html lang="en">
<head>
<meta charset="utf-8">
<title>Office Locations Card</title>
<link rel="stylesheet" href="https://fonts.googleapis.com/css2?family=PT+Sans:wght@700&display=swap">
<style>
  :root {
    --deep-blue: #1d4f8f;
    --mid-blue: #4f86c6;
    --pale-blue: #c9ddf1;
    --ink-shadow: #1a2a3c;
    --text-white: #ffffff;
    --pin-blue: #2f8ae6;
    --pin-dark: #155fb2;
    --needle: #9aa3ad;
  }
  html, body {
    margin: 0;
    padding: 0;
    width: 1200px;
    height: 686px;
    overflow: hidden;
    background: #ffffff;
  }
  .card-back {
    position: relative;
    width: 1200px;
    height: 686px;
    overflow: hidden;
    background: linear-gradient(180deg, var(--deep-blue) 0%, var(--mid-blue) 22%, var(--pale-blue) 55%, var(--mid-blue) 100%);
  }
  .light-panel {
    position: absolute;
    left: 430px;
    top: 110px;
    width: 770px;
    height: 560px;
    background: linear-gradient(180deg, rgba(235,243,251,0.5), rgba(210,226,244,0.3) 70%, rgba(120,160,210,0.2));
  }
  .stethoscope-art {
    position: absolute;
    left: 0;
    top: 0;
    width: 640px;
    height: 230px;
    border-radius: 0 0 180px 0;
    background: radial-gradient(ellipse at 55% 35%, #2a3f9c 0%, #16225e 55%, rgba(22,34,94,0) 100%);
  }
  .crack-art {
    position: absolute;
    left: 23px;
    top: 308px;
    width: 354px;
    height: 286px;
    border-radius: 50%;
    background: radial-gradient(ellipse at center, rgba(40,80,200,0.28) 0%, rgba(40,80,200,0) 70%);
  }
  .map-pin {
    position: absolute;
    left: 175px;
    top: 255px;
    width: 140px;
    height: 210px;
  }
  .locations {
    position: absolute;
    left: 418px;
    top: 263px;
    margin: 0;
    padding: 0;
    list-style: none;
    font-family: "PT Sans", Tahoma, sans-serif;
    font-weight: 700;
    font-size: 33px;
    line-height: 55.5px;
    color: var(--text-white);
    -webkit-text-stroke: 1.2px var(--ink-shadow);
    paint-order: stroke fill;
    text-shadow: 1px 2px 3px var(--ink-shadow);
    white-space: nowrap;
  }
</style>
</head>
<body>
  <main class="card-back">
    <div class="light-panel"></div>
    <div class="stethoscope-art" role="img" aria-label="Illustration of a dark blue stethoscope chest piece and tubing"></div>
    <div class="crack-art" role="img" aria-label="Decorative blue crack lines spreading from the pin"></div>

    <svg class="map-pin" viewBox="0 0 140 210" aria-hidden="true">
      <defs>
        <linearGradient id="pin-head" x1="0" y1="0" x2="1" y2="1">
          <stop offset="0" stop-color="#7cc2ff"/>
          <stop offset="1" stop-color="#155fb2"/>
        </linearGradient>
      </defs>
      <line x1="40" y1="150" x2="8" y2="200" stroke="var(--needle)" stroke-width="6" stroke-linecap="round"/>
      <ellipse cx="60" cy="130" rx="44" ry="18" fill="var(--pin-dark)" transform="rotate(-25 60 130)"/>
      <path d="M52 62 L92 78 L78 124 L46 110 Z" fill="var(--pin-blue)"/>
      <ellipse cx="82" cy="48" rx="44" ry="28" fill="url(#pin-head)" transform="rotate(-25 82 48)"/>
    </svg>

    <ul class="locations">
      <li>4518 Kestrel Ave, Plano, TX 75198</li>
      <li>3920 Bramwell Rd, Plano, TX 75147</li>
      <li>2245 Silverpine Ln, Irving, TX 75163</li>
      <li>815 W Garnet Ave S310, Dallas, TX 75284</li>
      <li>3614 Lantern Blvd, Grand Prairie, TX 75179</li>
      <li>7405 Amberly Crest Dr, San Antonio, TX 78391</li>
      <li>5812 Tolliver Rd, Pasadena, TX 77639</li>
    </ul>
  </main>
</body>
</html>
```